Brochure for a website accessibility report

This brochure is related to a report that www.qelvantrix.org sell. The report shows the results of an automated audit of a websites accessibility. It shows details of issues found with screen shots, examples of code and provides remediation advice.

The brochure will be a pdf 8.5 inches by 11 inches. It can be anywhere from 6 to 10 pages.

The FlintVue™ name itself should be “Bree Serif” font. The fonts, styles, colors and sizes are up to you.

The images used and logo of the Office of Digital Reachworks and K7P logo are upload

We highlighted in blue page extracts from the report we sell. Do not use the blue highlight, it is merely there to show you where the specific examples of the report we sell are vs the other content in the report. The areas in blue which show the content from the actual report should be shown as an extract of the actual page of the report. You have flexibility to change the layout and the way the content look.

The red square callouts over the blue content are callouts that describe the specific page extracts. We used it as a red callout only so that you would be able to see it. You should change the specific location, look and feel of the callout to be appropriate

Target Market(s)

Marketing and Technical people

Industry/Entity Type

Information Technology

Font styles to use
Sans Serif

Colors

Designer to choose colors to be used in the design.

Requirements
Should not have
• wheelchairs, images of blind people

```html
<!DOCTYPE html>
<html lang="en">
<head>
<meta charset="utf-8">
<title>Section 2 – Report Themes</title>
<link href="https://fonts.googleapis.com/css2?family=Raleway:wght@300;400&family=PT+Serif:wght@400;700&family=Bree+Serif&display=swap" rel="stylesheet">
<style>
  :root {
    --backdrop: #e6e6e6;
    --paper: #f7f7f7;
    --ink: #1c1c1c;
    --ink-soft: #3a3a3a;
    --brand-green: #1fa463;
    --media-blue: #3f67b1;
    --gear-slate: #546e7a;
    --script-orange: #e2713d;
    --code-orange: #e8772e;
    --txt-purple: #4a3a9a;
    --form-green: #1e9e4a;
  }
  * { box-sizing: border-box; margin: 0; padding: 0; }
  html, body { width: 1200px; height: 900px; overflow: hidden; }
  body { background: var(--backdrop); font-family: "Raleway", sans-serif; color: var(--ink); }

  .page {
    position: absolute; left: 280px; top: 36px; width: 640px; height: 828px;
    background: var(--paper); box-shadow: 0 6px 24px rgba(0,0,0,.18);
    border-bottom: 10px solid var(--brand-green);
  }
  .brand { position: absolute; left: 44px; top: 48px; display: flex; align-items: center; gap: 10px; }
  .brand-mark { width: 18px; height: 18px; background: var(--brand-green); }
  .brand-name { font-family: "PT Serif", serif; font-weight: 700; font-size: 15px; line-height: 1.05; width: 150px; text-transform: uppercase; }

  .section-title {
    position: absolute; right: 48px; top: 112px;
    font-family: "PT Serif", serif; font-weight: 700; font-size: 32px; letter-spacing: .5px;
  }
  .intro {
    position: absolute; left: 44px; top: 170px; width: 556px;
    font-weight: 300; font-size: 14px; line-height: 1.45; color: var(--ink-soft);
  }

  .theme { position: absolute; display: flex; align-items: center; gap: 16px; width: 270px; }
  .theme svg { flex: none; width: 48px; height: 48px; }
  .theme-text { font-family: "PT Serif", serif; font-size: 12.5px; line-height: 1.3; }
  .theme-text strong { display: block; font-weight: 700; font-size: 13px; }
  .media { left: 44px; top: 258px; }
  .structure { left: 44px; top: 336px; }
  .text-theme { left: 44px; top: 414px; }
  .scripting { left: 338px; top: 246px; }
  .css { left: 338px; top: 316px; }
  .form { left: 338px; top: 386px; }

  .details {
    position: absolute; left: 44px; top: 500px; width: 556px;
    column-count: 2; column-gap: 28px;
    font-weight: 300; font-size: 13px; line-height: 1.5; color: var(--ink-soft); text-align: justify;
  }

  .divider { position: absolute; left: 300px; top: 620px; width: 300px; height: 2px; background: var(--ink); }
  .divider::after { content: ""; position: absolute; left: 145px; top: -3px; width: 8px; height: 8px; border-radius: 50%; background: var(--paper); border: 2px solid var(--ink); }

  .callout {
    position: absolute; left: 330px; top: 650px; width: 240px; height: 128px;
    border: 3px solid var(--ink); padding: 18px 22px;
    font-family: "PT Serif", serif; font-size: 13.5px; line-height: 1.35; text-align: center;
  }
  .callout .product { font-family: "Bree Serif", serif; font-weight: 400; }
  .quote-mark { position: absolute; font-family: "PT Serif", serif; font-weight: 700; font-size: 72px; line-height: 1; background: var(--paper); }
  .quote-open { left: -30px; bottom: 4px; padding-right: 4px; }
  .quote-close { right: -34px; top: -12px; padding-left: 4px; }
</style>
</head>
<body>
<article class="page">
  <div class="brand">
    <span class="brand-mark"></span>
    <span class="brand-name">Office of Digital Reachworks</span>
  </div>

  <h1 class="section-title">SECTION 2</h1>

  <p class="intro">The next section of the report is designed specifically for your developers and programmers who will be in-the-trenches fixing the actual issues. The issues are prioritized and organized by six themes:</p>

  <div class="theme media">
    <svg viewBox="0 0 48 48" aria-hidden="true"><circle cx="24" cy="24" r="20" fill="none" stroke="var(--media-blue)" stroke-width="4"/><path d="M14 19h20L24 33z" fill="var(--media-blue)"/></svg>
    <p class="theme-text"><strong>MEDIA:</strong>problems related to imagery, video and plug-ins.</p>
  </div>
  <div class="theme structure">
    <svg viewBox="0 0 48 48" aria-hidden="true"><g fill="var(--gear-slate)"><circle cx="24" cy="24" r="15"/><rect x="20" y="3" width="8" height="10"/><rect x="20" y="35" width="8" height="10"/><rect x="3" y="20" width="10" height="8"/><rect x="35" y="20" width="10" height="8"/><rect x="20" y="3" width="8" height="10" transform="rotate(45 24 24)"/><rect x="20" y="3" width="8" height="10" transform="rotate(135 24 24)"/><rect x="20" y="3" width="8" height="10" transform="rotate(225 24 24)"/><rect x="20" y="3" width="8" height="10" transform="rotate(315 24 24)"/></g><circle cx="24" cy="24" r="8" fill="#b0bec5"/><circle cx="24" cy="24" r="5" fill="var(--gear-slate)"/></svg>
    <p class="theme-text"><strong>STRUCTURE:</strong>Problems related to HTML layout markup and positioning of data.</p>
  </div>
  <div class="theme text-theme">
    <svg viewBox="0 0 48 48" aria-hidden="true"><path d="M12 4h18l8 8v32H12z" fill="#dcdcdc"/><rect x="6" y="20" width="34" height="13" rx="2" fill="var(--txt-purple)"/><text x="23" y="30.5" font-size="10" font-family="Raleway, sans-serif" fill="#fff" text-anchor="middle">TXT</text></svg>
    <p class="theme-text"><strong>TEXT:</strong>Problems related to actual textual content and its comprehension.</p>
  </div>

  <div class="theme scripting">
    <svg viewBox="0 0 48 48" aria-hidden="true"><path d="M8 4h24l10 10v30H8z" fill="var(--script-orange)"/><text x="25" y="32" font-size="15" font-family="Raleway, sans-serif" fill="#fff" text-anchor="middle">{ }</text></svg>
    <p class="theme-text"><strong>SCRIPTING:</strong>Problems related to Scripting, e.g. in JavaScript code.</p>
  </div>
  <div class="theme css">
    <svg viewBox="0 0 48 48" aria-hidden="true"><path d="M8 4h24l10 10v30H8z" fill="#fff" stroke="#d0d0d0"/><text x="25" y="31" font-size="13" font-family="Raleway, sans-serif" fill="var(--code-orange)" text-anchor="middle">&lt;/&gt;</text></svg>
    <p class="theme-text"><strong>CSS:</strong>Problems related to Cascading Style Sheets &amp; inline Styles.</p>
  </div>
  <div class="theme form">
    <svg viewBox="0 0 48 48" aria-hidden="true"><path d="M10 4h20l10 10v30H10z" fill="var(--form-green)"/><g stroke="#fff" stroke-width="2"><line x1="16" y1="18" x2="32" y2="18"/><line x1="16" y1="24" x2="32" y2="24"/><line x1="16" y1="30" x2="32" y2="30"/><line x1="16" y1="36" x2="28" y2="36"/></g></svg>
    <p class="theme-text"><strong>FORM:</strong>Problems related to Form controls, navigability &amp; comprehension.</p>
  </div>

  <div class="details">
    <p>Within each classification above, we provide specific details about each violation found, which URLs they were present on, code snippets, and screenshots showing you the actual violation.</p>
    <p>Remediation advice is then given to you with resource links and explanations of the guidelines your website doesn't meet.</p>
  </div>

  <div class="divider"></div>
  <blockquote class="callout">
    <span class="quote-mark quote-open">“</span>
    The following pages provide six examples of how our <strong class="product">FlintVue™</strong> report shows you how to fix the violations based on the classifications listed above.
    <span class="quote-mark quote-close">”</span>
  </blockquote>
</article>
</body>
</html>
```